855 Bright Owl

Redesigning this front and back business card flyer and keeping the info but making it look better.

This is all about using the info and logo on the business card design and creating a better layout using any of the following and more.

Changing the background color or imagine, chaining the placement of content, resizing content.

Target Market(s)

Targeting people that have been injured on one side and people that have been giving a DUI on the other.

Contact Information for Business Card

We are looking to keep the info but make it look a fee cleaner and less cluttered

Font styles to use
Sans Serif

Requirements
Must have
• Must have the same info but a better layout.
Nice to have
• better background colors or image or layout. different fonts or same font all design options that will make it look professional and clean.

```html
<!DOCTYPE html>
<html lang="en">
<head>
<meta charset="utf-8">
<title>855 Bright Owl – Business Cards</title>
<link href="https://fonts.googleapis.com/css2?family=Archivo+Black&family=Arimo:wght@400;700&display=swap" rel="stylesheet">
<style>
  :root{
    --black:#0b0b0b;
    --red:#d41f2b;
    --white:#ffffff;
    --ink:#111111;
    --stage:#dcdde0;
    --photo-night:#3a2a2e;
    --photo-cast:#6f7378;
    --photo-room:#2c2f34;
  }
  *{box-sizing:border-box;margin:0;padding:0}
  html,body{width:1200px;height:800px;overflow:hidden}
  body{background:var(--stage);position:relative;font-family:"Arimo",Arial,sans-serif}
  .card{position:absolute;width:640px;height:366px;overflow:hidden;box-shadow:0 6px 18px rgba(0,0,0,.25)}
  .brand-name{font-family:"Archivo Black",Arial,sans-serif;color:var(--white);font-size:28px;letter-spacing:1px;line-height:1;white-space:nowrap;writing-mode:vertical-rl}

  /* Front: injury side */
  .card--injury{left:500px;top:30px;background:var(--black);color:var(--white)}
  .card--injury .brand-band{position:absolute;left:0;top:0;width:86px;height:100%;display:flex;align-items:center;justify-content:center}
  .photo-stack{position:absolute;left:96px;top:16px;width:150px;display:flex;flex-direction:column;gap:4px}
  .photo{height:108px}
  .photo--crash{background:linear-gradient(160deg,#5a2a33,var(--photo-night) 60%,#1a1416)}
  .photo--cast{background:linear-gradient(180deg,#8a8e93,var(--photo-cast) 60%,#3d4046)}
  .photo--recovery{background:linear-gradient(90deg,var(--photo-room),#8d939a 55%,var(--photo-room))}
  .injury-copy{position:absolute;left:266px;top:24px;right:18px}
  .injury-copy .lead{font-weight:700;font-size:21px}
  .injury-copy .headline{font-family:"Archivo Black",Arial,sans-serif;color:var(--red);font-size:34px;line-height:1.05;margin-top:2px}
  .ticks{list-style:none;margin-top:8px}
  .ticks li{position:relative;padding-left:16px;font-size:14px;line-height:1.3}
  .ticks li::before{content:"";position:absolute;left:0;top:4px;border-left:9px solid var(--red);border-top:5px solid transparent;border-bottom:5px solid transparent}
  .promise{font-weight:700;font-size:16px;margin-top:10px;line-height:1.25}
  .contact{display:flex;align-items:center;gap:10px;margin-top:12px}
  .contact .phone{font-weight:700;font-size:30px;letter-spacing:.5px}
  .site{font-size:19px;margin-top:2px}
  .site b{color:var(--red)}

  /* Back: DUI side */
  .card--dui{left:60px;top:404px;background:var(--white);color:var(--ink)}
  .card--dui .accent-stripe{position:absolute;left:0;top:0;width:14px;height:100%;background:var(--red)}
  .dui-headline{position:absolute;left:36px;top:26px;font-family:"Archivo Black",Arial,sans-serif;font-size:34px;line-height:.98}
  .dui-headline span{color:var(--red)}
  .dui-question{position:absolute;left:36px;top:202px;font-weight:700;font-size:19px;line-height:1.15}
  .dui-tips{position:absolute;left:232px;top:30px;width:300px}
  .dui-tips li{font-size:14px}
  .card--dui .contact{position:absolute;left:210px;top:268px;margin:0}
  .card--dui .site{position:absolute;left:210px;top:312px;font-size:20px}
  .card--dui .brand-band{position:absolute;right:0;top:0;width:100px;height:100%;background:var(--black);display:flex;align-items:center;justify-content:center}
  .card--dui .brand-name{transform:rotate(180deg)}
</style>
</head>
<body>

<section class="card card--injury">
  <div class="brand-band"><span class="brand-name">855 BRIGHT OWL</span></div>
  <div class="photo-stack">
    <div class="photo photo--crash" role="img" aria-label="Damaged car at a night crash scene with emergency lights"></div>
    <div class="photo photo--cast" role="img" aria-label="Person standing with a leg brace and crutches"></div>
    <div class="photo photo--recovery" role="img" aria-label="Silhouette of a person in a wheelchair by a window"></div>
  </div>
  <div class="injury-copy">
    <p class="lead">If You’ve Been Injured</p>
    <h1 class="headline">DON’T SETTLE</h1>
    <ul class="ticks">
      <li>for an inexperienced lawyer!</li>
      <li>for less than you deserve!</li>
      <li>for paying massive medical bills!</li>
      <li>for a life of pain and debt!</li>
    </ul>
    <p class="promise">We fight for you, so you<br>can focus on getting better</p>
    <div class="contact">
      <svg width="26" height="26" viewBox="0 0 26 26" aria-hidden="true"><circle cx="13" cy="13" r="13" fill="#d41f2b"/><path d="M9 7c1-1 2 0 2.6 1.4l.6 1.5c.3.8-.5 1.3-1 1.7.7 1.6 1.8 2.8 3.3 3.6.4-.5 1-1.3 1.8-1l1.6.7c1.3.6 2.1 1.6 1.1 2.6-1.4 1.5-3.4 1.3-5.6-.2-2.3-1.5-4-3.6-4.900-6-.6-1.8-.5-3.2.5-4.3z" fill="#fff"/></svg>
      <span class="phone">855-274-4869</span>
    </div>
    <p class="site">www.<b>855brightowl</b>.com</p>
  </div>
</section>

<section class="card card--dui">
  <div class="accent-stripe"></div>
  <h2 class="dui-headline">DON’T<br>SETTLE<br>FOR A<br><span>DUI</span></h2>
  <p class="dui-question">What Should<br>I Do If I Get<br>Pulled Over<br>For Dui?</p>
  <ul class="ticks dui-tips">
    <li>Pull over in a calm, normal manner</li>
    <li>Be polite at all times</li>
    <li>Do not admit to drinking</li>
    <li>Do not submit to any field sobriety tests</li>
    <li>Do not submit to taking a chemical test (breath, blood or urine)</li>
    <li>Do not make any statement after being arrested, especially when placed in the police cruiser</li>
  </ul>
  <div class="contact">
    <svg width="30" height="30" viewBox="0 0 26 26" aria-hidden="true"><circle cx="13" cy="13" r="13" fill="#d41f2b"/><path d="M9 7c1-1 2 0 2.6 1.4l.6 1.5c.3.8-.5 1.3-1 1.7.7 1.6 1.8 2.8 3.3 3.6.4-.5 1-1.3 1.8-1l1.6.7c1.3.6 2.1 1.6 1.1 2.6-1.4 1.5-3.4 1.3-5.6-.2-2.3-1.5-4-3.6-4.9-6-.6-1.8-.5-3.2.5-4.3z" fill="#fff"/></svg>
    <span class="phone">855-274-4869</span>
  </div>
  <p class="site">www.<b>855brightowl</b>.com</p>
  <div class="brand-band"><span class="brand-name">855 BRIGHT OWL</span></div>
</section>

</body>
</html>
```